Project Overview:
We are looking to create a website for a monthly subscription IPTV service in WordPress. The website should provide a seamless user experience for customers to sign up for the service and manage their account information. We need the following pages: Home Page, Product Page, Sign-Up Page, and Account Information Page.

Home Page:
The Home Page design should be simple and clean, with a dark theme and minimalistic design elements. We would like to include graphics of popular movie shows displayed on multiple devices. The page should highlight the key benefits and features of our service and provide a clear call-to-action for visitors to sign up.

Product Page:
The Product Page should provide detailed information about our subscription tiers and pricing plans. It should highlight the key features of each plan and provide a clear comparison between them. The page should also include a call-to-action button for visitors to sign up.

Sign-Up Page:
The Sign-Up Page is the conversion page where members will sign up for the service. It should collect the following information: Name, Phone Number, Email, Password, and Payment Information. The design should be simple, intuitive, and easy to use. It should highlight the benefits of our service and provide a clear call-to-action for visitors to sign up.

Account Information Page:
The Account Information Page should allow members to view and manage their account details. It should include the following information: Profile Image, Contact Details, Password Management, Payment Information Management, and Membership Expiration Date. The design should be user-friendly, intuitive, and easy to navigate.

Goals: The primary goal of the website is to provide an easy-to-use portal for customers to sign up for the service and manage their account information. The website should be user-friendly and visually appealing to attract potential customers.

Scope: The scope of the project includes designing a home page, a sign-up page, an account information page, and a payment information page. The website should be designed to be responsive and accessible on desktop and mobile devices.

Design Preferences: The design should be clean, modern, and visually appealing. The use of a color palette that is consistent with the brand identity is recommended. The website should be easy to navigate and provide a clear call-to-action for users to sign up for the service.

FYI: The subscription service I am designing a website for is related to an IPTV service. IPTV stands for Internet Protocol Television, which is a digital television broadcasting protocol that uses the internet to deliver TV programs and videos to viewers. The website will allow customers to sign up for the IPTV service and access their account information such as user name and password, membership tier, name, and payment details. Please let me know if you have any further questions, and I would be happy to provide more details. Thank you!

Dear Designers,

Thank you for your participation in our project. After reviewing the designs received so far, we have decided to update the brief to better reflect our needs and preferences. We apologize for any confusion this may cause, but we believe that these changes will result in better design submissions and a more successful project overall.

The updated brief is as follows:

We are looking to create a website for WordPress.

Also, here is the updated Brief.

Project Title: WordPress Website Design for Monthly Subscription IPTV Service

Project Overview:
We are looking to create a website for a monthly subscription IPTV service. The website should provide a seamless user experience for customers to sign up for the service and manage their account information. We need the following pages: Home Page, Product Page, Sign-Up Page, and Account Information Page.

Home Page:

Product Page:

Sign-Up Page:

Account Information Page:

Design Preferences:
We prefer a dark theme with minimalistic design elements and hits of our logo colors. The website should be easy to use and navigate, with clear calls-to-action and simple, intuitive forms. The design should be optimized for mobile devices and load quickly.

We hope that these updates provide you with a clearer understanding of our requirements and preferences. Please let us know if you have any questions or concerns. We look forward to seeing your revised designs.

Thank you again for your participation.
We will guarantee this project as soon as we see something we like that meets the updated requirements.

The website's target audience is individuals who are interested in subscribing to the monthly service.

4 page

• One item for sale and a client profile section.

```html
<!DOCTYPE html>
<html lang="en">
<head>
<meta charset="utf-8">
<title>VIVIDCAST – Home</title>
<link href="https://fonts.googleapis.com/css2?family=Bangers&family=Lato:wght@400;700;900&family=Outfit:wght@400;500&display=swap" rel="stylesheet">
<style>
:root{
  --red:#ff0a0a;
  --ink:#1b1b1b;
  --white:#ffffff;
  --night:#0b0c12;
  --muted:#d9d9d9;
  --display:'Bangers', cursive;
  --body:'Lato', sans-serif;
  --ui:'Outfit', sans-serif;
}
*{margin:0;padding:0;box-sizing:border-box}
html,body{width:1200px;height:3009px;overflow:hidden}
body{position:relative;background:var(--white);font-family:var(--body);color:var(--ink)}
.abs{position:absolute}
a{color:inherit;text-decoration:none}

/* header */
.site-header{position:absolute;left:0;top:0;width:1200px;height:85px;background:var(--white);z-index:3}
.nav-link{position:absolute;top:30px;font-size:16px;color:#222}
.nav-link.active{color:var(--red);font-weight:700;font-size:17px;text-decoration:underline;text-underline-offset:4px}
.brand-box{position:absolute;left:447px;top:0;width:301px;height:113px;background:var(--white);border-radius:0 0 18px 18px;box-shadow:0 4px 10px rgba(0,0,0,.12);display:flex;align-items:center;justify-content:center;z-index:4}
.brand-name{font-family:var(--body);font-weight:900;color:var(--red);font-size:44px;letter-spacing:1px}

/* hero */
.hero{position:absolute;left:0;top:85px;width:1200px;height:621px;background:linear-gradient(110deg,#2a2f36 0%,#3b4650 30%,#1d2630 60%,#36434e 100%)}
.hero-panel{position:absolute;left:636px;top:102px;width:488px;height:412px;background:rgba(20,22,28,.45)}
.hero-title{position:absolute;left:694px;top:225px;width:440px;font-family:var(--display);color:var(--white);font-size:84px;line-height:84px;letter-spacing:1px}
.hero-text{position:absolute;left:694px;top:401px;width:400px;color:var(--white);font-size:16px;line-height:31px}
.btn{display:flex;align-items:center;justify-content:center;background:var(--red);color:var(--white);border-radius:30px;font-weight:700}
.hero-btn{position:absolute;left:694px;top:505px;width:125px;height:51px;font-family:var(--ui);font-size:19px;font-weight:500}

/* section titles */
.section-title{position:absolute;left:0;width:1200px;text-align:center;font-family:var(--display);font-size:36px;color:var(--ink);letter-spacing:.5px}

/* show cards */
.card{position:absolute;width:326px;height:264px;border-radius:22px;overflow:hidden}
.card-photo{position:absolute;inset:0}
.shade{position:absolute;inset:0;background:linear-gradient(180deg,rgba(0,0,0,0) 45%,rgba(0,0,0,.7) 100%)}
.show-name{position:absolute;left:31px;top:170px;font-family:var(--display);font-size:21px;color:var(--white)}
.show-year{position:absolute;left:31px;top:196px;font-size:17px;color:var(--white)}
.show-rating{position:absolute;left:31px;top:227px;font-size:12px;color:var(--white)}
.watch-btn{position:absolute;left:166px;top:187px;width:118px;height:42px;font-size:16px}
.play{position:absolute;left:139px;top:109px;width:48px;height:48px;border-radius:50%;background:rgba(255,255,255,.3);display:flex;align-items:center;justify-content:center}
.clip-name{position:absolute;left:0;width:326px;top:232px;text-align:center;font-family:var(--display);font-size:21px;color:var(--white)}

/* about */
.about{position:absolute;left:0;top:1143px;width:1200px;height:500px;background:linear-gradient(90deg,#0e0f14 0%,#191a24 50%,#22223a 100%)}
.about-title{position:absolute;left:98px;top:51px;font-family:var(--display);font-size:35px;color:var(--white)}
.about-text{position:absolute;left:98px;top:97px;width:525px;color:var(--white);font-size:16px;line-height:31px}
.read-btn{position:absolute;left:98px;top:391px;width:129px;height:47px;font-family:var(--display);font-size:19px;font-weight:400;letter-spacing:.5px}
.devices{position:absolute;left:643px;top:40px;width:461px;height:414px;border-radius:24px;background:radial-gradient(ellipse at 60% 55%,#1c7fa0 0%,#233a66 40%,rgba(30,30,60,0) 75%)}

/* faq */
.faq{position:absolute;left:0;top:2076px;width:1200px;height:596px;background:linear-gradient(180deg,#050505 0%,#111318 50%,#050505 100%)}
.faq-title{position:absolute;left:0;width:1200px;top:52px;text-align:center;font-family:var(--display);font-size:36px;color:var(--white)}
.faq-item{position:absolute;left:111px;width:977px;background:var(--white);border-radius:38px}
.faq-icon{position:absolute;left:23px;top:22px;width:30px;height:30px}
.faq-q{position:absolute;left:77px;top:24px;font-family:var(--ui);font-size:15px;color:#333}
.faq-q strong{font-weight:500;font-size:18px;color:var(--ink)}
.faq-a{position:absolute;left:75px;top:77px;width:860px;font-size:15px;line-height:28px;color:#333}

/* footer */
.footer-brand{position:absolute;left:430px;top:2732px;width:339px;height:102px;border:4px solid var(--ink);border-radius:16px;display:flex;align-items:center;justify-content:center}
.footer-brand .brand-name{font-size:52px}
.footer-nav{position:absolute;top:2874px;font-size:16px;color:#222}
.copyright{position:absolute;left:0;width:1200px;top:2935px;text-align:center;font-size:16px;color:#222}
</style>
</head>
<body>

<header class="site-header">
  <a class="nav-link active" style="left:98px">Home</a>
  <a class="nav-link" style="left:186px">Movie</a>
  <a class="nav-link" style="left:267px">Series</a>
  <a class="nav-link" style="left:350px">About Us</a>
  <a class="nav-link" style="left:785px">Tv Shows</a>
  <a class="nav-link" style="left:879px">Services</a>
  <a class="nav-link" style="left:967px">Blog</a>
  <a class="nav-link" style="left:1027px">Contact Us</a>
</header>
<div class="brand-box"><span class="brand-name">VIVIDCAST</span></div>

<section class="hero" role="img" aria-label="Woman operating a broadcast control desk in a studio filled with monitors">
  <div class="hero-panel"></div>
</section>
<h1 class="hero-title">WELCOME TO VIVIDCAST</h1>
<p class="hero-text">Lorem ipsum dolor sit amet, consectetur adipiscing elit, sed do eiusmod tempor incididunt ut labore et dolore magna aliqua.</p>
<a class="btn hero-btn">Sign Up</a>

<h2 class="section-title" style="top:752px">TV SHOWS</h2>

<article class="card" style="left:98px;top:811px">
  <div class="card-photo" role="img" aria-label="Viewer watching a television in a cozy living room" style="background:linear-gradient(160deg,#6a7d8c,#3b3f47 55%,#8a6c54)"></div>
  <div class="shade"></div>
  <div class="show-name">LOREM IPSUM</div><div class="show-year">2022</div><div class="show-rating">7.8 Rating</div>
  <a class="btn watch-btn">Watch Now</a>
</article>
<article class="card" style="left:437px;top:811px">
  <div class="card-photo" role="img" aria-label="Television showing a streaming menu in a living room" style="background:linear-gradient(160deg,#77808a,#3a3536 55%,#7d6a58)"></div>
  <div class="shade"></div>
  <div class="show-name">LOREM IPSUM</div><div class="show-year">2022</div><div class="show-rating">7.8 Rating</div>
  <a class="btn watch-btn">Watch Now</a>
</article>
<article class="card" style="left:776px;top:811px">
  <div class="card-photo" role="img" aria-label="Family cheering in front of the screen" style="background:linear-gradient(160deg,#2c3e55,#6b4a33 55%,#3a4258)"></div>
  <div class="shade"></div>
  <div class="show-name">LOREM IPSUM</div><div class="show-year">2022</div><div class="show-rating">7.8 Rating</div>
  <a class="btn watch-btn">Watch Now</a>
</article>

<section class="about">
  <h2 class="about-title">ABOUT US</h2>
  <p class="about-text">Sed ut perspiciatis unde omnis iste natus error sit voluptatem accusantium doloremque laudantium, totam rem aperiam, eaque ipsa quae ab illo inventore veritatis et quasi architecto beatae vitae dicta sunt explicabo. Nemo enim ipsam voluptatem quia voluptas sit aspernatur aut odit aut fugit, sed quia consequuntur magni dolores eos qui ratione voluptatem sequi nesciunt. Neque porro quisquam est, qui dolorem ipsum quaerat voluptatem. Ut enim ad minima veniam, quis nostrum exercitationem ullam corporis suscipit molestiae consequatur, vel illum qui dolorem eum fugiat quo voluptas nulla pariatur?</p>
  <a class="btn read-btn">READ MORE</a>
  <div class="devices" role="img" aria-label="Two smartphones showing the streaming app with a viewer facing a glowing screen"></div>
</section>

<h2 class="section-title" style="top:1687px">CONTINUE WATCHING</h2>

<article class="card" style="left:98px;top:1745px;height:265px">
  <div class="card-photo" role="img" aria-label="Couple watching a film on the sofa" style="background:linear-gradient(160deg,#3d3a3a,#6b5648 55%,#2d2b2d)"></div>
  <div class="shade"></div>
  <div class="play"><svg width="20" height="22" viewBox="0 0 20 22"><path d="M2 1 L19 11 L2 21 Z" fill="#fff"/></svg></div>
  <div class="clip-name">SED UT PERSPICIATIS</div>
</article>
<article class="card" style="left:437px;top:1745px;height:265px">
  <div class="card-photo" role="img" aria-label="Person holding a remote in front of a television" style="background:linear-gradient(160deg,#2c3036,#7d8a92 50%,#202226)"></div>
  <div class="shade"></div>
  <div class="play"><svg width="20" height="22" viewBox="0 0 20 22"><path d="M2 1 L19 11 L2 21 Z" fill="#fff"/></svg></div>
  <div class="clip-name">SED UT PERSPICIATIS</div>
</article>
<article class="card" style="left:776px;top:1745px;height:265px">
  <div class="card-photo" role="img" aria-label="Viewer browsing a wall of movie titles" style="background:linear-gradient(160deg,#1d2b3f,#3b5570 50%,#1a2230)"></div>
  <div class="shade"></div>
  <div class="play"><svg width="20" height="22" viewBox="0 0 20 22"><path d="M2 1 L19 11 L2 21 Z" fill="#fff"/></svg></div>
  <div class="clip-name">SED UT PERSPICIATIS</div>
</article>

<section class="faq">
  <h2 class="faq-title">FREQUENTLY ASKED QUESTIONS</h2>
  <div class="faq-item" style="top:117px;height:73px">
    <svg class="faq-icon" viewBox="0 0 30 30"><circle cx="15" cy="15" r="15" fill="#ff0a0a"/><path d="M15 8v14M8 15h14" stroke="#fff" stroke-width="3"/></svg>
    <p class="faq-q"><strong>Question 1:</strong> Sed ut perspiciatis unde omnis iste natus error sit?</p>
  </div>
  <div class="faq-item" style="top:208px;height:226px">
    <svg class="faq-icon" viewBox="0 0 30 30"><circle cx="15" cy="15" r="15" fill="#ff0a0a"/><path d="M8 15h14" stroke="#fff" stroke-width="3"/></svg>
    <p class="faq-q" style="font-size:17px"><strong>Question 2:</strong> Sed ut perspiciatis unde omnis iste natus error sit?</p>
    <p class="faq-a">There is no experience needed! You provide the idea, and our team provides the experts to help you launch your dream drink brand. We meet with you throughout the process to ensure that we help you create the highest-quality product.but you can reach out to our team based on your location to see if we can.</p>
  </div>
  <div class="faq-item" style="top:454px;height:72px">
    <svg class="faq-icon" viewBox="0 0 30 30"><circle cx="15" cy="15" r="15" fill="#ff0a0a"/><path d="M15 8v14M8 15h14" stroke="#fff" stroke-width="3"/></svg>
    <p class="faq-q"><strong>Question 3:</strong> Sed ut perspiciatis unde omnis iste natus error sit?</p>
  </div>
</section>

<footer>
  <div class="footer-brand"><span class="brand-name">VIVIDCAST</span></div>
  <a class="footer-nav" style="left:262px">Home</a>
  <a class="footer-nav" style="left:344px">Movie</a>
  <a class="footer-nav" style="left:425px">Series</a>
  <a class="footer-nav" style="left:508px">About Us</a>
  <a class="footer-nav" style="left:611px">Tv Shows</a>
  <a class="footer-nav" style="left:709px">Services</a>
  <a class="footer-nav" style="left:797px">Blog</a>
  <a class="footer-nav" style="left:860px">Contact Us</a>
  <p class="copyright">Copyrights@2023.VIVIDCAST.All Rights Reserved</p>
</footer>

</body>
</html>
```